Halvik - consultancy website

I need a new design for my webpage/presence [to be functioning with Wordpress - I have a programmer to set it up but not the design idea].
My company is Halvik - a consultancy firm focused on growth management for Swedish SME's primarily;. We call it Leadership toolkit for firms on the rise, kind of a doctor helping small become big. Contentwise, its a simple frontpage + 3-4 subpages with content re company/myself/focus etc. The new site should communicate a fresh, trustworthy take yet simple and functional on all devices [i.e. think UI compatible for mobile/tablet]. Current building parts/form elements are
a) existing logo and text elements
b) existing pictures
c) the yellowish color
colours and new ideas on pictures/positioning are welcome. I prefer a 'full width page' solution with centralised text elements but that's all up to you to suggest. Current site is a quickfix made by myself - now I'm moving it to a new platform so want to take the opportunity to make it
Nothing superspecial as it is a 2-man show; on the other hand I still want to have a modern & fresh reflection of my brand in digital environments. Help me out!
www.halvik-demo.se
Best
Lina Bergqvist

```html
<!DOCTYPE html>
<html lang="en">
<head>
<meta charset="utf-8">
<title>Halvik – Growth management consultancy</title>
<link rel="stylesheet" href="https://fonts.googleapis.com/css2?family=Arimo:ital,wght@0,400;0,700;1,400&family=Crimson+Text:wght@400&display=swap">
<style>
  :root{
    --accent:#f0a43a;
    --ink:#1d1d1d;
    --body:#444;
    --muted:#8a8a8a;
    --white:#fff;
    --dark:#1e1e1e;
    --darker:#111;
    --red:#d9342b;
    --social-a:#3b5a9a;
    --social-b:#3fb3e6;
    --social-c:#dd4b39;
  }
  *{box-sizing:border-box;margin:0;padding:0}
  html,body{width:750px;height:1200px;overflow:hidden;background:var(--white)}
  body{position:relative;font-family:"Arimo",Arial,sans-serif;color:var(--ink)}
  .abs{position:absolute}

  /* Header */
  .site-header{left:0;top:0;width:750px;height:72px;background:linear-gradient(#f4f7fa,#e9eef3)}
  .brand{left:62px;top:10px;font-family:"Crimson Text",Georgia,serif;color:var(--ink)}
  .brand-name{font-size:34px;line-height:38px}
  .brand-tag{font-size:9.5px;line-height:11px}
  .main-nav{right:61px;top:30px;display:flex;gap:22px;font-size:9px;font-weight:700}
  .main-nav a{color:var(--ink);text-decoration:none;position:relative}
  .main-nav a.active{color:#c8841d}
  .main-nav a.active::after{content:"";position:absolute;left:-12px;right:-12px;top:15px;height:2px;background:var(--accent)}

  /* Hero */
  .hero{left:0;top:72px;width:750px;height:312px;
    background:linear-gradient(180deg,#7d97ad 0%,#a7aa8e 20%,#b88a3e 45%,#8a5a1c 75%,#5c3a12 100%)}
  .hero-title{right:75px;top:202px;text-align:right;font-size:16.5px;font-weight:700;color:var(--white);line-height:23px}
  .hero-title span{background:rgba(0,0,0,.28);padding:0 3px}
  .hero-btn{left:616px;top:326px;width:65px;height:21px;background:#0d0d0d;color:var(--white);font-size:9px;line-height:21px;text-align:center}
  .hero-dots{left:707px;top:342px;display:flex;gap:3px}
  .hero-dots i{width:6px;height:6px;border-radius:50%;border:1px solid #333}
  .hero-dots i:first-child{background:#333}

  /* About */
  .about-title{left:0;top:410px;width:750px;text-align:center;font-size:16px;font-weight:700}
  .about-text{left:64px;top:443px;width:622px;text-align:center;font-size:7.3px;line-height:14px;color:var(--body)}
  .btn-accent{left:337px;top:515px;width:75px;height:22px;background:var(--accent);color:var(--white);font-size:8.5px;line-height:22px;text-align:center}

  /* Testimonials */
  .testimonials{left:0;top:581px;width:750px;height:225px;
    background:linear-gradient(180deg,#2b2220 0%,#3a2c26 50%,#1f1a18 100%)}
  .testi-title{left:0;top:602px;width:752px;text-align:center;color:var(--white);font-size:16px;font-weight:700}
  .avatar{left:344px;top:640px;width:64px;height:64px;border-radius:50%;background:linear-gradient(#9a9a9a,#5a5a5a);border:3px solid #2a2a2a}
  .quote-mark{color:#bdbdbd;font-size:46px;font-weight:700;line-height:1;font-family:Georgia,serif}
  .testi-text{left:150px;top:719px;width:452px;text-align:center;color:#e4e4e4;font-size:7.3px;font-style:italic;line-height:12.8px}
  .testi-name{left:0;top:766px;width:750px;text-align:center;color:var(--white);font-size:7px}
  .testi-name b{font-weight:700}
  .testi-name span{color:#bbb;font-size:6.3px}

  /* News */
  .news-title{left:60px;top:834px;font-size:15px;font-weight:700}
  .news-nav{top:828px;width:16px;height:14px}
  .news-card{top:883px;width:204px;height:90px}
  .news-img{left:0;top:0;width:98px;height:80px}
  .news-body{left:107px;top:0;width:93px}
  .news-head{font-size:7px;line-height:11px;color:var(--ink)}
  .news-date{font-size:5.5px;color:#555;margin-top:3px;padding-bottom:3px;border-bottom:1px solid #ddd}
  .news-desc{font-size:6.3px;line-height:8.5px;color:#666;margin-top:5px}
  .news-more{font-size:6px;color:var(--red);margin-top:7px;display:flex;align-items:center;gap:4px}

  /* Footer */
  .site-footer{left:0;top:1025px;width:750px;height:144px;background:var(--dark)}
  .foot-head{top:1050px;color:#eee;font-size:9px}
  .foot-divider{top:1051px;width:1px;height:99px;background:#3a3a3a}
  .social{top:1079px;width:45px;height:58px;color:var(--white);font-size:7.5px;text-align:center}
  .social i{display:block;width:24px;height:24px;border-radius:50%;background:rgba(255,255,255,.18);margin:9px auto 9px}
  .foot-text{color:#999;font-size:7px;line-height:12px}
  .mail-input{left:334px;top:1107px;width:124px;height:18px;background:var(--white);font-size:6px;color:#aaa;line-height:18px;padding-left:10px}
  .mail-btn{left:458px;top:1107px;width:21px;height:18px;background:var(--accent)}
  .foot-menu{left:607px;top:1077px;list-style:none;color:#ddd;font-size:7px;line-height:13.5px}
  .bottom-bar{left:0;top:1169px;width:750px;height:31px;background:var(--darker);color:#777;font-size:6.5px;text-align:center;line-height:31px}
</style>
</head>
<body>

<header class="site-header abs">
  <div class="brand abs">
    <div class="brand-name">Halvik</div>
    <div class="brand-tag">Leadership toolkit for firms on the rise</div>
  </div>
  <nav class="main-nav abs">
    <a class="active" href="#">Home</a>
    <a href="#">About Us</a>
    <a href="#">Services</a>
    <a href="#">Gallery</a>
    <a href="#">Contact Us</a>
  </nav>
</header>

<section class="hero abs" role="img" aria-label="Close-up of golden wheat ears in a field under a blue sky"></section>
<h1 class="hero-title abs"><span>We are a consultancy firm focused on growth</span><br><span>management for Swedish SME's</span></h1>
<div class="hero-btn abs">Read More</div>
<div class="hero-dots abs"><i></i><i></i><i></i></div>

<h2 class="about-title abs">About Halvik</h2>
<p class="about-text abs">Lorem ipsum dolor sit amet, consectetur adipiscing elit. Fusce tristique ultricies dui et porta. Sed luctus mauris at dictum auctor. Ut sit amet eleifend tortor, vel fermentum ante. Sed luctus tellus eget tortor mollis, in ullamcorper erat facilisis. Pellentesque bibendum nec nisi ut consectetur. Mauris et elit id est luctus dapibus laoreet scelerisque arcu. Nam varius tincidunt enim quis ultricies. Morbi eleifend, dui faucibus gravida pellentesque, dui lectus tristique ante, et tempor metus ante ut mauris. Quisque feugiat massa ut nisi iaculis pulvinar. Ut euismod mauris enim, ac ultrices massa dignissim ac.</p>
<div class="btn-accent abs">View More</div>

<section class="testimonials abs" role="img" aria-label="Night city skyline with a suspension bridge, darkened"></section>
<h2 class="testi-title abs">Testimonials</h2>
<div class="avatar abs" role="img" aria-label="Portrait photo of the client giving the testimonial"></div>
<svg class="abs" style="left:18px;top:684px" width="16" height="28" viewBox="0 0 16 28"><path d="M14 1 2 14l12 13" fill="none" stroke="#ddd" stroke-width="1.2"/></svg>
<svg class="abs" style="left:716px;top:684px" width="16" height="28" viewBox="0 0 16 28"><path d="M2 1l12 13L2 27" fill="none" stroke="#ddd" stroke-width="1.2"/></svg>
<div class="quote-mark abs" style="left:128px;top:693px">“</div>
<div class="quote-mark abs" style="left:600px;top:749px">”</div>
<p class="testi-text abs">Mauris interdum velit leo, ac porta leo vehicula sed. Maecenas iaculis cursus magna. Vestibulum molestie, urna vel lobortis dictum, lacus nibh varius elit, ac tristique sapien dui sit amet diam. Phasellus hendrerit, augue vitae tristique rhoncus, felis urna blandit mauris, vel egestas ex tellus quis leo. Morbi at lacus in</p>
<p class="testi-name abs"><b>Oskar,</b> <span>Lorme ipsum</span></p>

<h2 class="news-title abs">Latest News</h2>
<svg class="news-nav abs" style="left:654px" viewBox="0 0 16 14"><rect width="16" height="14" fill="#f0a43a"/><path d="M9 4 6 7l3 3" fill="none" stroke="#fff" stroke-width="1.2"/></svg>
<svg class="news-nav abs" style="left:672px" viewBox="0 0 16 14"><rect width="16" height="14" fill="#1d1d1d"/><path d="M7 4l3 3-3 3" fill="none" stroke="#fff" stroke-width="1.2"/></svg>

<article class="news-card abs" style="left:62px">
  <div class="news-img abs" role="img" aria-label="Two businessmen reviewing a tablet at an office desk" style="background:linear-gradient(135deg,#d8d6d2,#8d8272)"></div>
  <div class="news-body abs">
    <div class="news-head">Lorem ipsum dolor sit amet, consectetur</div>
    <div class="news-date">15/05/2016 &nbsp;-&nbsp; Friday</div>
    <div class="news-desc">Mauris interdum velit leo, ac porta leo vehicula sed. Maecenas iaculis</div>
    <div class="news-more">Read More <svg width="7" height="7" viewBox="0 0 8 8"><circle cx="4" cy="4" r="3.4" fill="none" stroke="#d9342b" stroke-width=".8"/><path d="M3 2.4 4.6 4 3 5.6" fill="none" stroke="#d9342b" stroke-width=".8"/></svg></div>
  </div>
</article>

<article class="news-card abs" style="left:273px">
  <div class="news-img abs" role="img" aria-label="Business handshake over documents" style="background:linear-gradient(135deg,#2f5d8f,#c9d4e0)"></div>
  <div class="news-body abs">
    <div class="news-head">Lorem ipsum dolor sit amet, consectetur</div>
    <div class="news-date">15/05/2016 &nbsp;-&nbsp; Friday</div>
    <div class="news-desc">Mauris interdum velit leo, ac porta leo vehicula sed. Maecenas iaculis</div>
    <div class="news-more">Read More <svg width="7" height="7" viewBox="0 0 8 8"><circle cx="4" cy="4" r="3.4" fill="none" stroke="#d9342b" stroke-width=".8"/><path d="M3 2.4 4.6 4 3 5.6" fill="none" stroke="#d9342b" stroke-width=".8"/></svg></div>
  </div>
</article>

<article class="news-card abs" style="left:484px">
  <div class="news-img abs" role="img" aria-label="Team meeting silhouetted against a bright office window" style="background:linear-gradient(135deg,#cfd6d8,#e8dcb8 50%,#4a4a44)"></div>
  <div class="news-body abs">
    <div class="news-head">Lorem ipsum dolor sit amet, consectetur</div>
    <div class="news-date">15/05/2016 &nbsp;-&nbsp; Friday</div>
    <div class="news-desc">Mauris interdum velit leo, ac porta leo vehicula sed. Maecenas iaculis</div>
    <div class="news-more">Read More <svg width="7" height="7" viewBox="0 0 8 8"><circle cx="4" cy="4" r="3.4" fill="none" stroke="#d9342b" stroke-width=".8"/><path d="M3 2.4 4.6 4 3 5.6" fill="none" stroke="#d9342b" stroke-width=".8"/></svg></div>
  </div>
</article>

<footer class="site-footer abs"></footer>
<div class="foot-head abs" style="left:61px">Let's Connect</div>
<div class="foot-head abs" style="left:334px">Mailing List</div>
<div class="foot-head abs" style="left:607px">Menu</div>
<div class="foot-divider abs" style="left:273px"></div>
<div class="foot-divider abs" style="left:546px"></div>

<div class="social abs" style="left:62px;background:var(--social-a)"><i></i>2598</div>
<div class="social abs" style="left:111px;background:var(--social-b)"><i></i>4576</div>
<div class="social abs" style="left:161px;background:var(--social-c)"><i></i>1269</div>

<p class="foot-text abs" style="left:334px;top:1075px;width:150px">Sign up for our mailing list to get latest updates and offers.</p>
<div class="mail-input abs">Email address</div>
<svg class="mail-btn abs" viewBox="0 0 21 18"><rect width="21" height="18" fill="#f0a43a"/><path d="M7.5 9l2.2 2.2 4-4.4" fill="none" stroke="#fff" stroke-width="1.4"/></svg>
<p class="foot-text abs" style="left:334px;top:1128px">We respect your privacy</p>

<ul class="foot-menu abs">
  <li>Home</li><li>About Us</li><li>Services</li><li>Gallery</li><li>Contact Us</li>
</ul>

<div class="bottom-bar abs">© Copyrights 2015 All Rights Reserved</div>

</body>
</html>
```